Beverage Bottle Label

Startup juice company needs simple/clean/modern label design for two different bottles - 8 oz & 16 oz. Please see draft label attached (which includes label sizes). First page is front label and second page is back label. Also attached is photo of actual bottle (16 oz size) as well as a shampoo label to show potentially desired aesthetic of how words are separated into different sections. Final label will likely be high gloss white with black printed wording as seen in attached "image".

```html
<!DOCTYPE html>
<html lang="en">
<head>
<meta charset="utf-8">
<title>Sunmill Juicery – Bottle Labels</title>
<link rel="stylesheet" href="https://fonts.googleapis.com/css2?family=Arvo:wght@700&family=Sorts+Mill+Goudy&family=Mulish:wght@400;700&display=swap">
<style>
  :root {
    --bg-top: #f4f4f4;
    --bg-bottom: #dcdcdc;
    --berry: #8c1a2c;
    --berry-deep: #761425;
    --lime: #d6dd58;
    --lime-deep: #c3cb45;
    --ink: #161616;
  }
  * { margin: 0; padding: 0; box-sizing: border-box; }
  html, body { width: 1200px; height: 1000px; overflow: hidden; }
  body {
    position: relative;
    background: radial-gradient(ellipse at center, var(--bg-top) 0%, var(--bg-bottom) 100%);
    color: var(--ink);
    font-family: "Sorts Mill Goudy", Georgia, serif;
  }
  .label {
    position: absolute;
    border-radius: 18px;
  }
  .label--berry { background: linear-gradient(90deg, var(--berry-deep), var(--berry) 20%, var(--berry) 80%, var(--berry-deep)); }
  .label--lime { background: linear-gradient(90deg, var(--lime-deep), var(--lime) 20%, var(--lime) 80%, var(--lime-deep)); }
  .front { top: 110px; width: 260px; height: 830px; }
  .front--berry { left: 160px; }
  .front--lime { left: 478px; }
  .back { left: 790px; top: 150px; width: 228px; height: 720px; }

  .brand-seal {
    position: absolute;
    border-radius: 50%;
    background: var(--ink);
    display: flex; align-items: center; justify-content: center;
    font-family: "Sorts Mill Goudy", Georgia, serif;
    font-weight: 400;
    letter-spacing: 1px;
  }
  .front .brand-seal { left: 60px; top: 178px; width: 124px; height: 124px; font-size: 34px; }
  .front--berry .brand-seal { color: var(--berry); }
  .front--lime .brand-seal { color: var(--lime); }

  .vertical-name {
    position: absolute;
    left: 34px; top: 640px;
    transform: rotate(-90deg);
    transform-origin: left top;
    font-family: "Arvo", Georgia, serif;
    font-weight: 700;
    font-size: 21px;
    letter-spacing: 1.5px;
    white-space: nowrap;
  }
  .ingredients {
    position: absolute; left: 78px; top: 318px;
    list-style: none; font-size: 15.5px; line-height: 18px;
  }
  .organic-badge { position: absolute; left: 96px; top: 500px; width: 80px; height: 80px; border-radius: 50%; background: var(--ink); }
  .claims {
    position: absolute; left: 58px; top: 590px;
    display: grid; grid-template-columns: 70px 100px; row-gap: 1px;
    font-size: 10.5px; line-height: 13px;
  }
  .claims span::before { display: inline-block; width: 10px; font-size: 10px; margin-right: 2px; }
  .claims .yes::before { content: "☑"; }
  .claims .no::before { content: "☒"; }
  .shake { position: absolute; left: 0; width: 100%; top: 666px; text-align: center; font-size: 15px; line-height: 18px; }
  .perishable { position: absolute; left: 0; width: 100%; top: 718px; text-align: center; font-size: 9.5px; letter-spacing: .5px; }
  .volume { position: absolute; left: 0; width: 100%; top: 752px; text-align: center; font-size: 10px; line-height: 13px; }

  .back .brand-seal { left: 80px; top: 140px; width: 66px; height: 66px; font-size: 18px; color: var(--berry); }
  .back-copy {
    position: absolute; left: 38px; top: 232px; width: 160px;
    font-family: "Mulish", Arial, sans-serif; font-size: 8.2px; line-height: 12px; color: #3a0a12;
  }
  .back-copy p { margin-bottom: 8px; text-align: justify; }
  .back-copy h3 { font-size: 8.2px; font-weight: 700; color: var(--ink); margin-top: 4px; }
  .back-copy ul { list-style: none; }
  .back-copy li::before { content: "• "; }
  .back-copy .web { margin-top: 10px; }
  .back-copy .web strong { font-size: 11px; color: var(--ink); }
  .recycle { display: flex; align-items: center; gap: 6px; margin-top: 14px; font-size: 5px; line-height: 6px; color: var(--ink); font-weight: 700; }
  .fine-print { margin-top: 8px; font-size: 5px; line-height: 7px; text-align: justify; }
</style>
</head>
<body>
  <section class="label label--berry front front--berry">
    <div class="brand-seal">SMJ</div>
    <div class="vertical-name">SUNMILL JUICERY</div>
    <ul class="ingredients">
      <li>Golden</li><li>Radiance</li><li>Carrot</li><li>Pineapple</li><li>Orange</li><li>Grapefruit</li><li>Lemon</li>
    </ul>
    <div class="organic-badge" role="img" aria-label="Raw organic cold-pressed seal"></div>
    <div class="claims">
      <span class="yes">Vegan</span><span></span>
      <span class="yes">Gluten Free</span><span class="no">Unpasteurized</span>
      <span class="yes">Dairy Free</span><span class="no">No HPP</span>
      <span class="yes">Soy-Free</span><span class="no">Not Cold-Pressured</span>
    </div>
    <p class="shake">Separation is natural.<br>Shake well &amp; enjoy!</p>
    <p class="perishable">PERISHABLE. KEEP REFRIGERATED.</p>
    <p class="volume">16 Fl. Oz.<br>473ml</p>
  </section>

  <section class="label label--lime front front--lime">
    <div class="brand-seal">SMJ</div>
    <div class="vertical-name">SUNMILL JUICERY</div>
    <ul class="ingredients">
      <li>Golden</li><li>Radiance</li><li>Carrot</li><li>Pineapple</li><li>Orange</li><li>Grapefruit</li><li>Lemon</li>
    </ul>
    <div class="organic-badge" role="img" aria-label="Raw organic cold-pressed seal"></div>
    <div class="claims">
      <span class="yes">Vegan</span><span></span>
      <span class="yes">Gluten Free</span><span class="no">Unpasteurized</span>
      <span class="yes">Dairy Free</span><span class="no">No HPP</span>
      <span class="yes">Soy-Free</span><span class="no">Not Cold-Pressured</span>
    </div>
    <p class="shake">Separation is natural.<br>Shake well &amp; enjoy!</p>
    <p class="perishable">PERISHABLE. KEEP REFRIGERATED.</p>
    <p class="volume">16 Fl. Oz.<br>473ml</p>
  </section>

  <section class="label label--berry back">
    <div class="brand-seal">SMJ</div>
    <div class="back-copy">
      <p>At SMJ we make nutrition delicious and convenient, helping you and your loved ones maintain a healthier lifestyle on a busy schedule. Our organic juices are raw and cold-pressed to ensure maximum nutrition, quality and taste.</p>
      <p>Enjoy as a daily dietary supplement, and in no time at all your body will actually yearn for it. Thank you for allowing SMJ to help you nourish, empower and thrive!</p>
      <h3>Try your favorite SMJ beverage:</h3>
      <ul>
        <li>As a morning drink to energize and start your day naturally.</li>
        <li>As a healthy snack in between meals to curb your appetite.</li>
        <li>Before or after a workout to hydrate and nourish.</li>
        <li>As a cleanse package for one or more days to detoxify and reboot.</li>
      </ul>
      <p class="web">Visit us at <strong>www.sunmilljuicery.com</strong><br>to learn more!</p>
      <div class="recycle">
        <svg width="14" height="14" viewBox="0 0 14 14" aria-hidden="true"><path d="M7 1 L10 6 H4 Z M2 8 H6 L4 12 Z M8 12 L12 8 V12 Z" fill="none" stroke="#161616" stroke-width="1.2"/></svg>
        <svg width="12" height="14" viewBox="0 0 12 14" aria-hidden="true"><rect x="5" y="4" width="6" height="9" fill="#161616"/><circle cx="3" cy="2" r="1.5" fill="#161616"/><path d="M3 4 V10 M3 6 L5 7" stroke="#161616" stroke-width="1.2"/></svg>
        <span>THIS BOTTLE IS BPA FREE AND MADE OF THE MOST EASILY RECYCLED PLASTIC.</span>
      </div>
      <p class="fine-print">PERISHABLE. KEEP REFRIGERATED. This product is unpasteurized and has not been treated to reduce harmful bacteria, which may cause serious illness in children, the elderly and persons with weakened immune systems. Pregnant women should consult their physician before drinking. In case of a broken seal, do not consume.</p>
    </div>
  </section>
</body>
</html>
```